2021 Summer Ads Hollis Bay Custom Homes

We need a re-design of our summer ad run for our customer, Hollis Bay Custom Homes. They are custom home builders in the mostly rural parts of West Virginia, USA. They are known for their "Forever Home" tagline. We'd like two designed ads with the main difference being just the custom home that's featured. These designs should be for a Zintrola banner like 300 x 250 and square ad like 250 x 250. For inspiration please visit the Hollis Bay Custom Homes website at www dot hollisbaycustomhomes dot com

Target Market(s)

consumers / new home shoppers

Industry/Entity Type

Consumer

Requirements
Must have
• HBCH logo
Price Lock Available!
Custom home pic
Learn more >
small CFRM logo mark

```html
<!DOCTYPE html>
<html lang="en">
<head>
<meta charset="utf-8">
<title>Hollis Bay Custom Homes – Forever Home Ad</title>
<link href="https://fonts.googleapis.com/css2?family=Montserrat:wght@500;600;700;800&display=swap" rel="stylesheet">
<style>
  :root {
    --navy: #181b29;
    --navy-deep: #10121c;
    --stripe: #2a2d3d;
    --red: #d4182b;
    --red-dark: #8f1020;
    --white: #ffffff;
    --photo-sky: #c9b7b4;
    --photo-wall: #e9e6e1;
    --photo-stone: #a47d5e;
    --photo-ground: #9a6e4c;
  }
  * { margin: 0; padding: 0; box-sizing: border-box; }
  html, body {
    width: 1200px; height: 1200px; overflow: hidden;
    background: var(--navy);
  }
  .ad {
    position: relative; width: 1200px; height: 1200px; overflow: hidden;
    background: var(--navy);
    font-family: "Montserrat", sans-serif; color: var(--white);
  }
  .ad__backdrop { position: absolute; inset: 0; width: 1200px; height: 1200px; }
  .brand {
    position: absolute; left: 48px; top: 70px;
    display: flex; align-items: center; gap: 18px;
  }
  .brand__mark { width: 34px; height: 34px; background: var(--white); }
  .brand__name {
    font-weight: 700; font-size: 44px; line-height: 1.05;
    letter-spacing: 1px; text-transform: uppercase; width: 420px;
  }
  .headline {
    position: absolute; left: 40px; top: 288px;
    font-weight: 800; text-transform: uppercase; line-height: 1.22;
    white-space: nowrap;
  }
  .headline__lead { display: block; font-size: 68px; font-weight: 600; letter-spacing: 0.5px; }
  .headline__main { display: block; font-size: 70px; letter-spacing: 0; }
  .offer {
    position: absolute; left: 40px; top: 580px;
    font-weight: 800; font-size: 36px; text-transform: uppercase; letter-spacing: 0.5px;
    white-space: nowrap;
  }
  .cta {
    position: absolute; left: 40px; top: 690px;
    width: 400px; height: 110px;
    background: var(--red); border-radius: 10px;
    display: flex; align-items: center; justify-content: space-between;
    padding: 0 24px 0 50px;
    font-weight: 800; font-size: 30px; text-transform: uppercase; letter-spacing: 1px;
    color: var(--white); text-decoration: none; white-space: nowrap;
    box-shadow: 0 8px 22px rgba(0,0,0,0.35);
  }
  .cta__arrow {
    width: 68px; height: 68px; border-radius: 50%; background: var(--white);
    display: flex; align-items: center; justify-content: center;
  }
  .member {
    position: absolute; left: 42px; top: 912px; width: 260px;
  }
  .member__name {
    font-weight: 800; font-size: 84px; line-height: 1; letter-spacing: 2px;
  }
  .member__full {
    margin-top: 10px; font-weight: 500; font-size: 24px; line-height: 1.2;
  }
</style>
</head>
<body>
<main class="ad">
  <svg class="ad__backdrop" viewBox="0 0 1200 1200" xmlns="http://www.w3.org/2000/svg">
    <defs>
      <linearGradient id="photoTone" x1="0" y1="0" x2="0" y2="1">
        <stop offset="0" stop-color="var(--photo-sky)"/>
        <stop offset="0.35" stop-color="var(--photo-wall)"/>
        <stop offset="0.7" stop-color="var(--photo-stone)"/>
        <stop offset="1" stop-color="var(--photo-ground)"/>
      </linearGradient>
      <linearGradient id="panelFade" x1="0" y1="0" x2="1" y2="1">
        <stop offset="0" stop-color="var(--navy)"/>
        <stop offset="1" stop-color="var(--navy-deep)"/>
      </linearGradient>
    </defs>
    <rect class="panel" width="1200" height="1200" fill="url(#panelFade)"/>
    <polygon class="panel-stripe" points="300,0 520,0 -40,1200 -260,1200" fill="var(--stripe)" opacity="0.55"/>
    <polygon class="panel-stripe" points="760,0 840,0 350,1200 270,1200" fill="var(--stripe)" opacity="0.6"/>
    <g role="img" aria-label="Photo of a white two-storey custom home with a dark blue roof, screened porches and stone-clad columns at dusk">
      <polygon points="930,0 1200,0 1200,1200 480,1200" fill="url(#photoTone)"/>
    </g>
    <polygon class="accent-stripe" points="850,0 930,0 480,1200 400,1200" fill="var(--red)"/>
    <polygon class="accent-stripe-shade" points="820,0 850,0 400,1200 370,1200" fill="var(--red-dark)"/>
  </svg>

  <div class="brand">
    <span class="brand__mark"></span>
    <span class="brand__name">Hollis Bay Custom Homes</span>
  </div>

  <h1 class="headline">
    <span class="headline__lead">Start Building</span>
    <span class="headline__main">Your Forever</span>
    <span class="headline__main">Home Today!</span>
  </h1>

  <p class="offer">Price Lock Available!</p>

  <a class="cta" href="#">
    <span class="cta__label">Learn More</span>
    <span class="cta__arrow">
      <svg width="30" height="30" viewBox="0 0 24 24" aria-hidden="true">
        <path d="M8 4 L16 12 L8 20" fill="none" stroke="var(--red)" stroke-width="4" stroke-linecap="round" stroke-linejoin="round"/>
      </svg>
    </span>
  </a>

  <div class="member">
    <div class="member__name">CFRM</div>
    <div class="member__full">Council of Fine Residential Makers</div>
  </div>
</main>
</body>
</html>
```